Basic business card

use my newly created logo - and the phrases (Lower Cost of Test & Accelarated New Product Introduction) - and my new email domain / ID - use at conferences / tradeshows

Industry/Entity Type

semiconductor

Contact Information for Business Card

Daniel K Forde, Owner, communicate via Logo - Lower COT - Cost of Test, Accelerated NPI - New Product Introduction, phone +1 555 613 0946, Chandler, Arizona, USA, daniel.forde@qal-vub.com

Font styles to use
Sans Serif

Requirements
Nice to have
• re-use my logo created via Pixel Harbor last August (#7315926)

```html
<!DOCTYPE html>
<html lang="en">
<head>
<meta charset="utf-8">
<title>QAL-VUB Business Card</title>
<link rel="stylesheet" href="https://fonts.googleapis.com/css2?family=Open+Sans:wght@400;600;700&display=swap">
<style>
  :root {
    --bg: #252527;
    --card: #212125;
    --card-mark: #2c2c31;
    --green: #7dc540;
    --orange: #f39a1f;
    --white: #ffffff;
    --slate: #4b5670;
  }
  * { margin: 0; padding: 0; box-sizing: border-box; }
  html, body { width: 1200px; height: 780px; overflow: hidden; background: var(--bg); }
  body { font-family: "Open Sans", Arial, sans-serif; position: relative; }

  .card {
    position: absolute;
    top: 230px;
    width: 560px;
    height: 320px;
    background: var(--card);
    border: 3px solid var(--green);
    border-radius: 18px;
    overflow: hidden;
  }
  .card--front { left: 27px; }
  .card--back { left: 613px; }

  .brand { position: absolute; display: flex; align-items: center; gap: 12px; font-weight: 600; letter-spacing: 1px; }
  .brand__square { display: block; }
  .card--front .brand { left: 0; right: 0; top: 0; bottom: 0; justify-content: center; font-size: 54px; color: var(--card-mark); }
  .card--front .brand__square { width: 38px; height: 38px; background: var(--card-mark); }
  .card--back .brand { left: 34px; top: 148px; font-size: 30px; color: var(--slate); }
  .card--back .brand__square { width: 22px; height: 22px; background: var(--slate); }

  .divider { position: absolute; left: 292px; top: 64px; width: 2px; height: 180px; background: var(--white); }

  .details { position: absolute; left: 318px; top: 58px; color: var(--white); }
  .details__name { font-size: 23px; font-weight: 700; line-height: 1; white-space: nowrap; }
  .details__first { color: var(--green); }
  .details__last { color: var(--orange); }
  .details__title { font-size: 12.5px; font-weight: 600; margin-top: 6px; }
  .details__address { font-size: 11.5px; line-height: 1.45; margin-top: 14px; }
  .contact { list-style: none; margin-top: 14px; font-size: 11.5px; }
  .contact li { display: flex; align-items: center; gap: 8px; height: 19px; }
  .contact svg { width: 12px; height: 12px; flex: none; }

  .bands { position: absolute; left: 0; bottom: 0; width: 554px; height: 80px; }
</style>
</head>
<body>

<section class="card card--front" aria-label="Card front">
  <div class="brand"><span class="brand__square"></span>QAL-VUB</div>
</section>

<section class="card card--back" aria-label="Card back">
  <div class="brand"><span class="brand__square"></span>QAL-VUB</div>

  <div class="divider"></div>

  <div class="details">
    <p class="details__name"><span class="details__first">Lena</span> <span class="details__last">Marvik</span></p>
    <p class="details__title">Managing Director</p>
    <p class="details__address">1480 Harbor Line Dr. Suite<br>310 Mesa Ridge, TX 75555</p>
    <ul class="contact">
      <li>
        <svg viewBox="0 0 24 24"><path fill="#7dc540" d="M6.6 10.8a15 15 0 0 0 6.6 6.6l2.2-2.2c.3-.3.7-.4 1-.2 1.1.4 2.3.6 3.6.6.6 0 1 .4 1 1V20c0 .6-.4 1-1 1A17 17 0 0 1 3 4c0-.6.4-1 1-1h3.5c.6 0 1 .4 1 1 0 1.3.2 2.5.6 3.6.1.3 0 .7-.2 1z"/></svg>
        (555) 284-3019
      </li>
      <li>
        <svg viewBox="0 0 24 24"><rect x="2" y="5" width="20" height="14" rx="2" fill="#7dc540"/><path d="M3 6l9 7 9-7" fill="none" stroke="#212125" stroke-width="2"/></svg>
        info@lumen-site.com
      </li>
      <li>
        <svg viewBox="0 0 24 24"><circle cx="12" cy="12" r="10" fill="#7dc540"/><path d="M2 12h20M12 2c3 3 3 17 0 20M12 2c-3 3-3 17 0 20" fill="none" stroke="#212125" stroke-width="1.5"/></svg>
        www.lumen-site.com
      </li>
    </ul>
  </div>

  <svg class="bands" viewBox="0 0 554 80" aria-hidden="true">
    <path d="M300 8 H554 V26 H340 Q326 26 316 20 Z" fill="#f39a1f"/>
    <path d="M0 46 H318 Q330 46 336 40 L350 40 L330 64 H0 Z" fill="#7dc540"/>
  </svg>
</section>

</body>
</html>
```